Velmora Consulting Business

** Please add the content information from my old business card
1. I would like to see a two sided business card with both options with the 1st Option--Tallow Spire-new WHITE BACKGROUND LOGO
2 nd Option-Tallow Spire - new BLACK- Background Logo
3rd -Option a business card with my Photo on the card
Please add the new word to the card information:
EXECUTION
AS THE OWNER'S REP
WE AIM TO ACHIEVE YOUR
INFRASTRUCTURE VISION with
OUR SPECIALIZATION & EXECUTION in:

FUNDING Planning
BUSINESS Planning
INFRASTRUCTURE Planning
PROJECT Management
Since 2012
_____________________________________________________________________
I want to get spot uv raised printing. I was liking a a nice rich white linen paper stock with black writing & NOT A COLORED CARD other than a variety of white or black cards concept

```html
<!DOCTYPE html>
<html lang="en">
<head>
<meta charset="utf-8">
<title>Velmora Consulting – Business Card</title>
<link href="https://fonts.googleapis.com/css2?family=Montserrat:wght@500;600;700&display=swap" rel="stylesheet">
<style>
  :root {
    --backdrop: #d4d5d7;
    --card: #0a0a0a;
    --ink: #ffffff;
    --accent: #e8223f;
    --photo-top: #2a2420;
    --photo-bottom: #0d0d0d;
  }
  * { margin: 0; padding: 0; box-sizing: border-box; }
  html, body {
    width: 1200px; height: 900px; overflow: hidden;
    background: var(--backdrop);
    font-family: "Montserrat", sans-serif;
    color: var(--ink);
  }
  .card {
    position: absolute; top: 115px;
    width: 383px; height: 670px;
    background: var(--card);
    border-radius: 14px;
    overflow: hidden;
  }
  .card--front { left: 182px; }
  .card--back { left: 669px; }
  .line {
    position: absolute; left: 0; right: 0;
    text-align: center; white-space: nowrap;
  }
  .accent { color: var(--accent); }

  /* Front */
  .brand-name {
    top: 178px; font-size: 66px; font-weight: 600; letter-spacing: -1px;
    display: flex; justify-content: center; align-items: center; gap: 12px;
  }
  .brand-dot { width: 16px; height: 16px; background: var(--accent); display: inline-block; }
  .brand-sub { top: 257px; font-size: 19px; font-weight: 500; letter-spacing: 14px; padding-left: 14px; }
  .pitch { font-size: 16px; font-weight: 600; letter-spacing: 0.3px; }
  .services { font-size: 16px; font-weight: 500; display: flex; justify-content: center; align-items: center; gap: 9px; }
  .bullet { width: 10px; height: 10px; background: var(--accent); display: inline-block; }
  .since { top: 611px; font-size: 19px; font-weight: 700; color: var(--accent); letter-spacing: 0.8px; }

  /* Back */
  .portrait {
    position: absolute; left: 36px; top: 20px; width: 311px; height: 366px;
    background: radial-gradient(ellipse at 50% 35%, var(--photo-top), var(--photo-bottom) 70%);
  }
  .person-name { top: 412px; font-size: 22px; font-weight: 700; color: var(--accent); letter-spacing: 0.3px; }
  .person-role { top: 442px; font-size: 16px; font-weight: 500; letter-spacing: 0.6px; }
  .contact-icons { top: 486px; display: flex; justify-content: center; gap: 8px; }
  .phone { top: 514px; font-size: 18px; font-weight: 500; letter-spacing: 3px; }
  .email { top: 542px; font-size: 17px; font-weight: 500; letter-spacing: 0.5px; }
  .web { top: 565px; font-size: 21px; font-weight: 700; color: var(--accent); letter-spacing: 3.5px; }
  .location { top: 617px; font-size: 18px; font-weight: 500; letter-spacing: 0.5px; }
</style>
</head>
<body>
  <section class="card card--front">
    <div class="line brand-name"><span>Velmora</span><span class="brand-dot"></span></div>
    <div class="line brand-sub">CONSULTING</div>

    <div class="line pitch" style="top:310px">EXECUTION AS THE <span class="accent">OWNER'S REP</span></div>
    <div class="line pitch" style="top:342px">WE AIM TO ACHIEVE YOUR</div>
    <div class="line pitch" style="top:375px">INFRASTRUCTURE VISION with</div>
    <div class="line pitch" style="top:407px">OUR SPECIALIZATION &amp; EXECUTION in:</div>

    <div class="line services" style="top:464px"><span class="bullet"></span>FUNDING Planning</div>
    <div class="line services" style="top:501px"><span class="bullet"></span>BUSINESS Planning</div>
    <div class="line services" style="top:539px"><span class="bullet"></span>INFRASTRUCTURE Planning</div>
    <div class="line services" style="top:577px"><span class="bullet"></span>PROJECT Management</div>

    <div class="line since">Since 2012</div>
  </section>

  <section class="card card--back">
    <div class="portrait" role="img" aria-label="Portrait photo of the company CEO"></div>
    <div class="line person-name">Maren Ellsworth-Dhaliwal</div>
    <div class="line person-role">CEO / LEAD PROJECT MANAGER</div>

    <div class="line contact-icons">
      <svg width="16" height="16" viewBox="0 0 16 16" aria-label="Phone"><path d="M3 1.5l3 .5 1 3-1.8 1.4a8 8 0 0 0 4.4 4.4L11 9l3 1 .5 3-1.5 1.5C7 14.5 1.5 9 1.5 3z" fill="#e8223f"/></svg>
      <svg width="18" height="16" viewBox="0 0 18 16" aria-label="Email"><rect x="1" y="3" width="16" height="11" fill="#e8223f"/><path d="M1 3l8 6 8-6" stroke="#0a0a0a" stroke-width="1.5" fill="none"/></svg>
      <svg width="16" height="16" viewBox="0 0 16 16" aria-label="Website"><circle cx="8" cy="8" r="7" fill="#e8223f"/><path d="M1 8h14M8 1c-3 3.5-3 10.5 0 14M8 1c3 3.5 3 10.5 0 14" stroke="#0a0a0a" stroke-width="1" fill="none"/></svg>
    </div>

    <div class="line phone">867.555.0148</div>
    <div class="line email">maren@velmora.ca</div>
    <div class="line web">www.velmora.ca</div>
    <div class="line location">Greyhollow Bay · Ambermoor Point</div>
  </section>
</body>
</html>
```